Brand new letterhead, business card, email signature etc.

We are a financial company in London, UK. Our website is www.marlowvane.com. We're wanting a complete remodel of the company colours, letter head, business cards, email signatures, etc. Looking to keep the same font for the company name. I have upload a colour palette that we want to work with. We're looking for company letterhead for outgoing letters/ correspondence, letterhead for internal documentation, email signatures, e-letters. etc. Ultimately we will redesign the entire website also. It is important that our clients get a strong, secure, warm, trustworthy, solid feeling and first impression.
Updates

Designs look the same

Target Market(s)

Institutional investors, (ultra) high net worth individuals

Industry/Entity Type

Finance, Invesments banking.

Font styles to use
Other font styles liked:
• Current font is "Champagne & Limousines"

Requirements
Must have
• Must use the colours provided on the PDF uploaded to the portal. The purple = main colour. The red = accent colour.
Nice to have
• Nice to use same font as now for the company name "Corvane". Font is "Champagne & Limousines". Nice to have some reference to the old logo flower, but only subtle.
Should not have
• Do not use the colour red from our website. Use the colours provided on the colour palette PDF that I uploaded in the portal.

```html
<!DOCTYPE html>
<html lang="en">
<head>
<meta charset="utf-8">
<title>Corvane – Business Card</title>
<link rel="stylesheet" href="https://fonts.googleapis.com/css2?family=Arimo:wght@400;700&display=swap">
<style>
  :root {
    --backdrop: #e4e4e4;
    --plum: #2b0019;
    --plum-light: #3a0425;
    --accent: #d93516;
    --paper: #f7f7f7;
    --ink: #1e1e1e;
    --mute: #b98aa6;
  }
  * { margin: 0; padding: 0; box-sizing: border-box; }
  html, body { width: 1200px; height: 1200px; overflow: hidden; }
  body {
    background: var(--backdrop);
    font-family: "Arimo", Arial, sans-serif;
    position: relative;
  }
  .card {
    position: absolute;
    left: 262px;
    width: 686px;
    height: 392px;
    overflow: hidden;
  }
  .card-front { top: 165px; background: var(--plum); }
  .card-back {
    top: 653px;
    background: linear-gradient(180deg, var(--plum-light), var(--plum));
  }
  .front-shapes { position: absolute; inset: 0; width: 100%; height: 100%; }
  .brand {
    position: absolute;
    left: 49px;
    top: 61px;
    display: flex;
    align-items: center;
    gap: 16px;
  }
  .brand-square {
    width: 66px; height: 66px;
    border: 1px solid var(--ink);
  }
  .brand-name {
    font-size: 37px;
    font-weight: 400;
    letter-spacing: 7px;
    color: var(--ink);
    text-transform: uppercase;
  }
  .address, .contacts {
    position: absolute;
    left: 48px;
    font-size: 17px;
    line-height: 21.5px;
    color: var(--ink);
  }
  .address { top: 175px; }
  .contacts { top: 229px; list-style: none; }
  .contacts li { display: flex; align-items: center; gap: 8px; }
  .contacts svg { width: 15px; height: 15px; fill: var(--accent); flex: none; }
  .holder {
    position: absolute;
    right: 55px;
    top: 297px;
    text-align: right;
  }
  .holder-name {
    font-size: 26px;
    font-weight: 700;
    color: var(--accent);
    line-height: 30px;
  }
  .holder-role {
    font-size: 17px;
    color: var(--paper);
    line-height: 22px;
  }
  .back-name {
    position: absolute;
    inset: 0;
    display: flex;
    align-items: center;
    justify-content: center;
    font-size: 40px;
    letter-spacing: 10px;
    color: var(--mute);
    text-transform: uppercase;
  }
</style>
</head>
<body>
  <section class="card card-front">
    <svg class="front-shapes" viewBox="0 0 800 457" preserveAspectRatio="none" aria-hidden="true">
      <path d="M0,457 C470,402 705,210 715,0 H0 Z" fill="var(--accent)" stroke="var(--paper)" stroke-width="2"/>
      <path d="M0,457 C430,396 650,205 660,0 H0 Z" fill="var(--paper)"/>
    </svg>

    <div class="brand">
      <div class="brand-square"></div>
      <span class="brand-name">Corvane</span>
    </div>

    <p class="address">27 Aldermere Lane<br>Kelby Heath, KT4 9RN</p>

    <ul class="contacts">
      <li>
        <svg viewBox="0 0 24 24"><path d="M6.6 10.8a15.1 15.1 0 0 0 6.6 6.6l2.2-2.2c.3-.3.7-.4 1-.2 1.1.4 2.3.6 3.6.6.6 0 1 .4 1 1V20c0 .6-.4 1-1 1A17 17 0 0 1 3 4c0-.6.4-1 1-1h3.5c.6 0 1 .4 1 1 0 1.3.2 2.5.6 3.6.1.3 0 .7-.2 1z"/></svg>
        (418) 5206-7391
      </li>
      <li>
        <svg viewBox="0 0 24 24"><path d="M2 5h20v14H2z M3.5 6.5 12 13l8.5-6.5" fill="none" stroke="var(--accent)" stroke-width="2"/><path d="M3 6h18l-9 7z"/></svg>
        name@MARLOWVANE.com
      </li>
      <li>
        <svg viewBox="0 0 24 24"><circle cx="12" cy="12" r="10"/><path d="M8 7c2 0 3 1 2 3s1 3 3 3-1 4-3 5M15 5c0 2 2 3 4 3" fill="none" stroke="var(--paper)" stroke-width="1.6"/></svg>
        www.marlowvane.com
      </li>
    </ul>

    <div class="holder">
      <p class="holder-name">Elliot Harrow</p>
      <p class="holder-role">President</p>
    </div>
  </section>

  <section class="card card-back">
    <span class="back-name">Corvane</span>
  </section>
</body>
</html>
```